Harbor Loom Floors Letterhead

Letterhead used for business reasons. It must be editable and easy to use.

Address is 2715 W. Pelican Lane Englewood FL 34187 - 941.382.6519

```html
<!DOCTYPE html>
<html lang="en">
<head>
<meta charset="utf-8">
<title>Harbor Loom Floors Letterhead</title>
<link href="https://fonts.googleapis.com/css2?family=Lato:wght@400;700&family=Montserrat:wght@400&family=Italianno&display=swap" rel="stylesheet">
<style>
  :root {
    --backdrop: #e4e4e4;
    --paper: #ffffff;
    --brand-orange: #e08b26;
    --brand-taupe: #968a84;
    --ink: #1c1c1c;
    --ink-soft: #2a2a2a;
  }
  * { margin: 0; padding: 0; box-sizing: border-box; }
  html, body {
    width: 1200px; height: 1079px; overflow: hidden;
    background: var(--backdrop);
  }
  .letterhead {
    position: absolute; left: 232px; top: 20px;
    width: 735px; height: 1039px;
    background: var(--paper);
    box-shadow: 0 4px 14px rgba(0,0,0,0.18);
    font-family: "Lato", sans-serif;
    color: var(--ink);
  }
  .brand-name {
    position: absolute; left: 37px; top: 50px;
    font-family: "Lato", sans-serif; font-weight: 400;
    font-size: 31px; line-height: 34px;
    color: var(--brand-orange);
  }
  .contact {
    position: absolute; left: 532px; top: 80px;
    height: 55px; border-left: 1.5px solid var(--brand-orange);
    padding-left: 23px;
    font-family: "Montserrat", sans-serif; font-size: 13px;
    line-height: 17.5px; color: var(--ink-soft);
  }
  .contact .phone { margin-top: 9px; display: flex; align-items: center; gap: 5px; margin-left: -2px; }
  .contact .phone svg { width: 11px; height: 11px; }
  .letter-text { position: absolute; left: 37px; font-size: 15px; line-height: 17.5px; }
  .date { top: 257px; }
  .recipient { top: 293px; }
  .company-address { top: 364px; }
  .salutation { top: 450px; font-size: 19px; font-weight: 700; }
  .body-copy {
    position: absolute; left: 37px; top: 513px; width: 661px;
    font-size: 14px; line-height: 16.2px; text-align: justify;
  }
  .body-copy p + p { margin-top: 16.5px; }
  .closing { top: 809px; }
  .signature {
    position: absolute; left: 37px; top: 882px;
    font-family: "Italianno", cursive; font-size: 42px; color: #111;
  }
  .footer-wave { position: absolute; left: 0; bottom: 0; width: 735px; height: 103px; display: block; }
</style>
</head>
<body>
  <main class="letterhead">
    <header>
      <div class="brand-name">Harbor Loom<br>Floors</div>
      <address class="contact" style="font-style:normal">
        <div>2715 W. Pelican Lane</div>
        <div>Englewood FL 34187</div>
        <div class="phone">
          <svg viewBox="0 0 24 24" aria-hidden="true"><path fill="var(--brand-orange)" d="M6.6 10.8a15.1 15.1 0 0 0 6.6 6.6l2.2-2.2a1 1 0 0 1 1-.25 11.4 11.4 0 0 0 3.6.57 1 1 0 0 1 1 1V20a1 1 0 0 1-1 1A17 17 0 0 1 3 4a1 1 0 0 1 1-1h3.5a1 1 0 0 1 1 1c0 1.25.2 2.45.57 3.57a1 1 0 0 1-.25 1z"/></svg>
          <span>941.382.6519</span>
        </div>
      </address>
    </header>

    <div class="letter-text date">January-03-2020</div>
    <div class="letter-text recipient">Mr, John Doe<br>President</div>
    <div class="letter-text company-address">Link Corppration<br>123 Street Name, Suite# 10<br>City, State, 120023</div>
    <div class="letter-text salutation">Dear Mr, John</div>

    <section class="body-copy">
      <p>Lorem ipsum dolor sit amet, consectetur adipiscing elit, sed do eiusmod tempor incididunt ut labore et dolore magna aliqua. Ut enim ad minim veniam, quis nostrud exercitation ullamco laboris nisi ut aliquip ex ea commodo consequat. Duis aute irure dolor in reprehenderit in voluptate velit esse cillum dolore eu fugiat nulla pariatur.</p>
      <p>Lorem ipsum dolor sit amet, consectetur adipiscing elit, sed do eiusmod tempor incididunt ut labore et dolore magna aliqua. Ut enim ad minim veniam, quis nostrud exercitation ullamco laboris nisi ut aliquip ex ea commodo consequat. Duis aute irure dolor in reprehenderit in voluptate velit esse cillum dolore eu fugiat nulla pariatur.</p>
      <p>Lorem ipsum dolor sit amet, consectetur adipiscing elit, sed do eiusmod tempor incididunt ut labore et dolore magna aliqua. Ut enim ad minim veniam, quis nostrud exercitation ullamco laboris nisi ut aliquip ex ea commodo consequat.</p>
      <p>Excepteur sint occaecat cupidatat non proident, sunt in culpa qui officia deserunt mollit anim id est laborum. re et dolore magnam aliquam quaerat voluptatem.</p>
    </section>

    <div class="letter-text closing">Regards</div>
    <div class="signature">Michel Smith</div>

    <svg class="footer-wave" viewBox="0 0 1004 140" preserveAspectRatio="none" aria-hidden="true">
      <path fill="var(--brand-taupe)" d="M0,62 C150,108 300,98 500,60 C650,30 730,10 820,14 C900,18 950,42 990,66 L1004,140 L0,140Z"/>
      <path fill="var(--paper)" d="M0,70 C150,107 300,102 500,67 C650,37 730,30 820,34 C900,38 960,62 1004,76 L1004,140 L0,140Z"/>
      <path fill="var(--brand-orange)" d="M0,80 C150,117 300,112 500,77 C650,47 730,40 820,44 C900,48 960,72 1004,86 L1004,140 L0,140Z"/>
    </svg>
  </main>
</body>
</html>
```